Islamic App which helps to calculate, track and pay Zakat

We need an application which helps muslim people to calculate and pay Zakat - mandatory donations which muslim should pay based on his income. The application will consist of two parts (applications) - the one which is used by "payer" and another one - used by "receiver". To make a payment "payer" will scan QR-code which "receiver" will generate in his app and show to payer. "Receiver" will have option to initiate cash withdrawal once he collected required minimum for the withdrawal.
Important that "payer" side journey to make a payment should be as short as possible - imaging same as you make donation by cash - you just gave money and left, similar experience should be with app - couple-three taps to make it. For receiver side major requirement is to keep the UI/UX as simple as possible, these guys usually are not aware about online payments (roughly speaking this part of the app should be more similar to Quillotap rather than to banking/financial app)
In this Figma I tried to sketch the UX for both sides (just to explain the idea): https://www.plovix.com/file/Rt4mWq8ZpLbN2vKe7sJd3X/Plovix-basics?type=design&node-id=2741-583016&mode=design

Target Market(s)

Muslims

Industry/Entity Type

Donations

Colors
0094D4
00A9DD
6FCCEA
C7EBF8
E9F6FB
00AB8E
00BBA5
67D7C9
C6EFE9
E9F9F6

Requirements
Must have
• The application should have soul. Design should show that this application intend to help people, not just money transfer
Nice to have
• Payment should be as quick as possible, in the sketches I showed it as banknotes/coins which user need to slide-up to pay. Maybe make it similar as Vel OS dock icons?
Should not have
• The application should not look as banking/financial app or wallet app

```html
<!DOCTYPE html>
<html lang="en">
<head>
<meta charset="utf-8">
<title>Zakat App Screens</title>
<link rel="stylesheet" href="https://fonts.googleapis.com/css2?family=Poppins:wght@400;500;600;700&family=Roboto:ital,wght@0,400;0,500;0,700;1,400&display=swap">
<style>
:root{
  --stage:#858384;
  --screen:#ffffff;
  --header:#2a5a88;
  --ink:#222222;
  --muted:#555555;
  --line:#d6d6d6;
  --btn-dark:#17238a;
  --btn-light:#6f92e2;
  --accent:#2c49b4;
  --avatar:#d8dcf3;
  --city-sky:#e9eef3;
  --city-mid:#b8c6d2;
  --city-low:#8ea3b4;
  --photo-sky:#cfdde8;
  --photo-tile:#5d7fb0;
  --photo-stone:#c69a5a;
}
*{box-sizing:border-box;margin:0;padding:0}
html,body{width:1200px;height:785px;overflow:hidden;background:var(--stage)}
.canvas{position:relative;width:1200px;height:785px}
.screen{position:absolute;top:93px;width:276px;height:598px;background:var(--screen);border-radius:28px;overflow:hidden;font-family:Roboto,sans-serif;color:var(--ink)}
.screen--signin{left:98px}
.screen--code{left:462px}
.screen--profile{left:827px}
.app-header{position:absolute;top:0;left:0;width:276px;height:66px;z-index:3}
.app-header .brand{position:absolute;top:16px;left:0;width:100%;text-align:center;font-family:Poppins,sans-serif;font-weight:600;font-size:34px;color:#fff;line-height:1}
.city-backdrop{position:absolute;left:0;bottom:0;width:100%;height:200px;background:linear-gradient(180deg,rgba(255,255,255,0) 0%,var(--city-sky) 30%,var(--city-mid) 70%,var(--city-low) 100%)}
.title{position:absolute;left:0;width:100%;text-align:center;font-family:Poppins,sans-serif;font-weight:600;font-size:28px;line-height:37px;color:var(--ink)}
.phone-field{position:absolute;left:22px;top:206px;width:236px;height:44px;border-bottom:1px solid var(--line);font-size:14px;padding-top:2px}
.helper{position:absolute;left:21px;top:265px;font-style:italic;font-size:12px;color:var(--muted)}
.primary-btn{position:absolute;left:14px;width:250px;height:44px;border-radius:22px;background:linear-gradient(90deg,var(--btn-dark),var(--btn-light));color:#fff;font-weight:700;font-size:15px;display:flex;align-items:center;justify-content:center;z-index:2}
.keypad{position:absolute;left:30px;width:216px;height:222px;background:#fff;border:1px solid #333;border-radius:8px;padding:14px 10px;display:grid;grid-template-columns:repeat(3,1fr);grid-template-rows:repeat(4,1fr);gap:14px 8px;z-index:2}
.key{border:1.5px solid #222;border-radius:6px;display:flex;align-items:center;padding-left:9px;gap:4px}
.key b{font-family:Roboto,sans-serif;font-weight:700;font-size:24px;line-height:1}
.key span{font-size:9px;margin-top:6px}
.sms-note{position:absolute;top:140px;left:0;width:100%;text-align:center;font-size:14px;line-height:22px;color:var(--ink)}
.code-boxes{position:absolute;top:226px;left:31px;display:flex;gap:10px}
.code-box{width:46px;height:42px;border:1.5px solid #bbb;border-radius:5px}
.hero-photo{position:absolute;top:70px;left:0;width:100%;height:330px;background:linear-gradient(180deg,var(--photo-sky) 0%,var(--photo-stone) 25%,var(--photo-tile) 50%,var(--photo-stone) 75%,rgba(255,255,255,0) 100%)}
.next-arrow{position:absolute;top:211px;left:244px;width:60px;height:60px;border-radius:50%;background:#fff;z-index:2}
.avatar{position:absolute;top:366px;left:35px;width:44px;height:44px;border-radius:50%;background:var(--avatar);display:flex;align-items:center;justify-content:center}
.name{position:absolute;top:414px;left:34px;font-family:Poppins,sans-serif;font-weight:700;font-size:29px;color:var(--ink)}
.bio{position:absolute;top:461px;left:34px;font-family:Poppins,sans-serif;font-size:15px;line-height:22px;color:var(--muted)}
.balance{position:absolute;top:526px;left:34px;font-family:Poppins,sans-serif;display:flex;align-items:flex-end;gap:4px}
.balance .amount{font-weight:700;font-size:30px;color:var(--accent);line-height:1}
.balance .currency{font-weight:600;font-size:15px;color:var(--ink);margin-bottom:-5px}
.withdraw-btn{position:absolute;top:519px;left:188px;width:48px;height:48px;border-radius:50%;background:linear-gradient(135deg,var(--btn-light),var(--btn-dark));display:flex;align-items:center;justify-content:center}
</style>
</head>
<body>
<main class="canvas">

  <section class="screen screen--signin">
    <svg class="app-header" viewBox="0 0 276 66"><path d="M0 0H276V22H242C242 46 214 63 190 63H86C62 63 34 46 34 22H0Z" fill="var(--header)"/></svg>
    <div class="app-header" style="pointer-events:none"><span class="brand">Zakat</span></div>
    <div class="city-backdrop" role="img" aria-label="Faded city skyline photo"></div>
    <h1 class="title" style="top:108px">Sign In to<br>Zakat App</h1>
    <div class="phone-field">+971 (50)000 -00-00</div>
    <p class="helper">Please enter your UAE number</p>
    <div class="primary-btn" style="top:309px">NEXT</div>
    <div class="keypad" style="top:363px">
      <div class="key"><b>1</b><span>_,@</span></div><div class="key"><b>2</b><span>ABC</span></div><div class="key"><b>3</b><span>DEF</span></div>
      <div class="key"><b>4</b><span>GHI</span></div><div class="key"><b>5</b><span>JKL</span></div><div class="key"><b>6</b><span>MNO</span></div>
      <div class="key"><b>7</b><span>PQRS</span></div><div class="key"><b>8</b><span>TUV</span></div><div class="key"><b>9</b><span>WXYZ</span></div>
      <div class="key"><b>*</b><span>␣</span></div><div class="key"><b>0</b></div><div class="key"><b>#</b></div>
    </div>
  </section>

  <section class="screen screen--code">
    <svg class="app-header" viewBox="0 0 276 66"><path d="M0 0H276V22H242C242 46 214 63 190 63H86C62 63 34 46 34 22H0Z" fill="var(--header)"/></svg>
    <div class="app-header" style="pointer-events:none"><span class="brand">Zakat</span></div>
    <div class="city-backdrop" role="img" aria-label="Faded city skyline photo"></div>
    <h1 class="title" style="top:108px">Input Code</h1>
    <p class="sms-note">We have sent an SMS with a<br>4 digit code to phone<br>+971 50 7284619</p>
    <div class="code-boxes"><div class="code-box"></div><div class="code-box"></div><div class="code-box"></div><div class="code-box"></div></div>
    <div class="primary-btn" style="top:287px">SIGN IN</div>
    <div class="keypad" style="top:359px">
      <div class="key"><b>1</b><span>_,@</span></div><div class="key"><b>2</b><span>ABC</span></div><div class="key"><b>3</b><span>DEF</span></div>
      <div class="key"><b>4</b><span>GHI</span></div><div class="key"><b>5</b><span>JKL</span></div><div class="key"><b>6</b><span>MNO</span></div>
      <div class="key"><b>7</b><span>PQRS</span></div><div class="key"><b>8</b><span>TUV</span></div><div class="key"><b>9</b><span>WXYZ</span></div>
      <div class="key"><b>*</b><span>␣</span></div><div class="key"><b>0</b></div><div class="key"><b>#</b></div>
    </div>
  </section>

  <section class="screen screen--profile">
    <div class="hero-photo" role="img" aria-label="Photo of a tiled mosque portal with minarets"></div>
    <svg class="app-header" viewBox="0 0 276 66"><path d="M0 0H276V22H242C242 46 214 63 190 63H86C62 63 34 46 34 22H0Z" fill="var(--header)"/></svg>
    <div class="app-header" style="pointer-events:none"><span class="brand">Zakat</span></div>
    <div class="next-arrow"><svg width="26" height="20" viewBox="0 0 26 20" style="position:absolute;left:7px;top:20px"><path d="M2 10H23M15 2L23 10L15 18" fill="none" stroke="#222" stroke-width="2"/></svg></div>
    <div class="avatar"><svg width="22" height="24" viewBox="0 0 22 24"><circle cx="11" cy="7" r="5" fill="none" stroke="var(--accent)" stroke-width="2"/><path d="M2 22V19C2 16 4 15 7 15H15C18 15 20 16 20 19V22Z" fill="none" stroke="var(--accent)" stroke-width="2"/></svg></div>
    <h2 class="name">Rafiq</h2>
    <p class="bio">I am from Pakistan.<br>I have thee Kids.</p>
    <div class="balance"><span class="amount">847</span><span class="currency">AED</span></div>
    <div class="withdraw-btn"><svg width="24" height="26" viewBox="0 0 24 26"><rect x="1" y="2" width="22" height="5" rx="1" fill="none" stroke="#fff" stroke-width="2"/><rect x="6" y="7" width="12" height="16" rx="1" fill="none" stroke="#fff" stroke-width="2"/><circle cx="12" cy="14" r="2.5" fill="none" stroke="#fff" stroke-width="1.6"/></svg></div>
  </section>

</main>
</body>
</html>
```